Harborview Estates Business Card for Apartment Buildings

Create business cards for resident managers who run apartment buildings. The audience is the public who are searching for apartment rentals, and current residents who live at the apartment building. Key design element will be incorporating the company logo, however, the logo cannot dominate. The building name and manager name are more important than the logo. Current business card design leaves little room for copy, so we may need to reduce the size on the current card to allow for more space for copy.

Target Market(s)

Adults 18-65 years of age, who are looking for an apartment rental, plus current residents who live at our apartment buildings.

Industry/Entity Type

Property Management

Contact Information for Business Card

A major design element will be use of the company logo. Important property and manager contact information must be part of the design. The size of the logo will need to be reduced to make room for building and manager contact copy.

Font styles to use
Sans Serif

Colors
3176b5
000000
959595
ffffff

Requirements
Must have
• 1) Incorporate the company logo.
• 2) Use the company colors (dark blue, black/grey, over white).
• 3) FEATURE THE BUILDING NAME
• 4) FEATURE THE MANAGER NAME
• 5) The company name is less important than BUILDING and MANAGER
• 6) Manager contact information
• **SEE ATTACHED CREATIVE BRIEF**
Nice to have
• 1) Back of card logo watermark
• 2) Ability to write notes on back of carfd
Should not have
• Avoid letting the company logo dominate the card, the building name and manager are more important than the company logo.

```html
<!DOCTYPE html>
<html lang="en">
<head>
<meta charset="utf-8">
<title>Harborview Estates – Resident Manager Business Card</title>
<link href="https://fonts.googleapis.com/css2?family=Roboto+Condensed:wght@700&family=Roboto:wght@400;500&display=swap" rel="stylesheet">
<style>
  :root {
    --brand-blue: #0f6aab;
    --brand-blue-light: #3176b5;
    --ink: #3a3a3a;
    --ink-soft: #4a4a4a;
    --rule: #959595;
    --paper: #f3f3f3;
    --backdrop: #2a2a2a;
    --strip: #3d3d3d;
    --white: #ffffff;
  }
  * { margin: 0; padding: 0; box-sizing: border-box; }
  html, body {
    width: 1200px; height: 960px; overflow: hidden;
    background: var(--backdrop);
    font-family: "Roboto", Arial, sans-serif;
  }
  .stage { position: relative; width: 1200px; height: 960px; }

  .card {
    position: absolute; left: 320px; width: 600px; height: 342px;
    overflow: hidden;
  }

  /* Back of card */
  .card-back { top: 108px; background: var(--brand-blue); }
  .card-back .watermark-dot {
    position: absolute; left: 448px; top: 90px;
    width: 40px; height: 40px; border-radius: 50%;
    background: rgba(255,255,255,0.12);
  }
  .card-back .watermark-name {
    position: absolute; left: 0; right: 0; top: 140px;
    text-align: center;
    font-family: "Roboto Condensed", Arial, sans-serif;
    font-weight: 700; font-size: 58px; letter-spacing: 1px;
    color: rgba(255,255,255,0.12);
  }

  /* Front of card */
  .card-front { top: 493px; background: var(--paper); }
  .company-mark {
    position: absolute; left: 62px; top: 150px;
    display: flex; align-items: center; gap: 10px;
  }
  .company-mark .dot {
    width: 18px; height: 18px; border-radius: 50%;
    background: var(--brand-blue);
  }
  .company-mark .company-name {
    font-family: "Roboto Condensed", Arial, sans-serif;
    font-weight: 700; font-size: 25px; color: var(--brand-blue);
  }

  .details { position: absolute; left: 332px; top: 64px; right: 0; }
  .manager-name {
    font-family: "Roboto Condensed", Arial, sans-serif;
    font-weight: 700; font-size: 24px; line-height: 28px;
    color: var(--brand-blue);
  }
  .manager-title {
    font-weight: 500; font-size: 15px; line-height: 20px;
    color: var(--ink); margin-top: 1px;
  }
  .rule { height: 1px; background: var(--rule); margin: 9px 0 10px; }
  .building-name {
    font-weight: 500; font-size: 15px; line-height: 18px;
    color: var(--brand-blue);
  }
  .address { font-size: 14.5px; line-height: 18px; color: var(--ink-soft); font-style: normal; }
  .contact-list { list-style: none; margin-top: -1px; }
  .contact-list li {
    display: flex; align-items: center; gap: 7px;
    font-size: 14.5px; line-height: 19.5px; color: var(--ink-soft);
  }
  .contact-list svg { width: 14px; height: 14px; fill: var(--brand-blue); flex: none; }

  .bottom-strip {
    position: absolute; left: 0; right: 0; bottom: 0; height: 7px;
    background: var(--strip);
  }
  .web-tab {
    position: absolute; left: 312px; bottom: 0; width: 244px; height: 27px;
    background: var(--brand-blue); border: 2px solid var(--white); border-bottom: none;
    color: var(--white); font-size: 14px; letter-spacing: 2.4px;
    display: flex; align-items: center; justify-content: center;
  }
</style>
</head>
<body>
<main class="stage">
  <section class="card card-back" aria-label="Card back">
    <div class="watermark-dot"></div>
    <div class="watermark-name">Harborview Estates</div>
  </section>

  <section class="card card-front" aria-label="Card front">
    <div class="company-mark">
      <span class="dot"></span>
      <span class="company-name">Harborview Estates</span>
    </div>

    <div class="details">
      <h1 class="manager-name">Marisol Delgado</h1>
      <p class="manager-title">Resident Manager</p>
      <div class="rule"></div>
      <h2 class="building-name">Crestline Garden Apartments</h2>
      <address class="address">2845 Linden Avenue<br>Riverside, CA 92507</address>
      <div class="rule"></div>
      <ul class="contact-list">
        <li>
          <svg viewBox="0 0 16 16" aria-hidden="true"><path d="M3.6 1.2l2.3 2.6-1.3 2a9 9 0 0 0 5.6 5.6l2-1.3 2.6 2.3-1.3 2.4C7.9 14.6 1.4 8.1 1.2 2.5z"/></svg>
          555-210-4836
        </li>
        <li>
          <svg viewBox="0 0 16 16" aria-hidden="true"><path d="M4.5 1h7a1 1 0 0 1 1 1v12a1 1 0 0 1-1 1h-7a1 1 0 0 1-1-1V2a1 1 0 0 1 1-1zm.6 1.8v9.4h5.8V2.8zM8 12.8a.8.8 0 1 0 0 1.6.8.8 0 0 0 0-1.6z"/></svg>
          555-374-9102
        </li>
        <li>
          <svg viewBox="0 0 16 16" aria-hidden="true"><path d="M4 1h7v4H4zM1 6h14v6h-2v3H3v-3H1zm3.5 4v3.5h7V10z"/></svg>
          555-648-3071
        </li>
        <li>
          <svg viewBox="0 0 16 16" aria-hidden="true"><path d="M1 3h14v1.2L8 8.6 1 4.2zm0 2.8l7 4.4 7-4.4V13H1z"/></svg>
          marisol@harborviewest.com
        </li>
      </ul>
    </div>

    <div class="bottom-strip"></div>
    <div class="web-tab">www.harborviewest.com</div>
  </section>
</main>
</body>
</html>
```